SkyvornQ Business Cards and Stationary Design

Need a design for our business cards and stationary. I want to carry on the theme of the logo. I want the business cards to have a design on the back. I would like the business cards and the stationary to carry the same theme, design scheme, and branding

Target Market(s)

Airlines and Maintenance Facilities

Industry/Entity Type

Aviation

Contact Information for Business Card

Name
Position Title
Address: 4827 Trellis Hollow Road, Calderwick Bay, Westmarch, 70412
Office Number
Mobile Number
Email
Website

Font styles to use
Serif
Sans Serif

Colors

Designer to choose colors to be used in the design.

```html
<!DOCTYPE html>
<html lang="en">
<head>
<meta charset="utf-8">
<title>SkyvornQ Business Card</title>
<link href="https://fonts.googleapis.com/css2?family=Open+Sans:wght@400;600;700&display=swap" rel="stylesheet">
<style>
  :root {
    --navy: #0b2f6b;
    --sky: #1ba3e3;
    --white: #ffffff;
    --ink: #1d2a44;
    --stage: #e8ebf0;
  }
  * { margin: 0; padding: 0; box-sizing: border-box; }
  html, body { width: 1200px; height: 900px; overflow: hidden; }
  body {
    background: var(--stage);
    font-family: "Open Sans", Arial, sans-serif;
    position: relative;
  }
  .card {
    position: absolute;
    width: 560px;
    height: 320px;
    border-radius: 18px;
    overflow: hidden;
    box-shadow: 0 10px 28px rgba(10, 30, 70, 0.18);
  }
  .card-front { left: 80px; top: 90px; background: var(--white); }
  .card-back { left: 560px; top: 490px; background: var(--navy); }

  .front-bands { position: absolute; inset: 0; }

  .brand {
    position: absolute;
    display: flex;
    align-items: center;
    gap: 12px;
    font-weight: 700;
    letter-spacing: 0.12em;
    text-transform: uppercase;
  }
  .brand-front { right: 34px; top: 48px; color: var(--navy); font-size: 30px; }
  .brand-mark {
    width: 34px; height: 34px;
    border-radius: 50%;
    border: 4px solid currentColor;
    flex: none;
  }

  .contact-address {
    position: absolute;
    right: 34px; top: 126px;
    text-align: right;
    font-style: normal;
    font-size: 12.5px;
    line-height: 1.45;
    color: var(--ink);
  }

  .website-front {
    position: absolute;
    right: 34px; top: 240px;
    color: var(--white);
    font-size: 13px;
    letter-spacing: 0.08em;
  }

  .person { position: absolute; left: 34px; top: 164px; }
  .person-name {
    color: var(--navy);
    font-weight: 700;
    font-size: 19px;
    letter-spacing: 0.01em;
    text-transform: uppercase;
  }
  .person-title { color: var(--ink); font-size: 13px; margin-bottom: 6px; }
  .contact-row {
    display: flex; align-items: center; gap: 8px;
    font-size: 13px; color: var(--ink); line-height: 1.5;
  }
  .contact-row svg { width: 11px; height: 11px; flex: none; }
  .email {
    position: absolute; left: 34px; bottom: 14px;
    display: flex; align-items: center; gap: 8px;
    color: var(--white); font-size: 13.5px;
  }
  .email svg { width: 13px; height: 10px; }

  .back-content {
    position: absolute; inset: 0;
    display: flex; flex-direction: column;
    align-items: center; justify-content: center;
    gap: 26px;
  }
  .brand-back { position: static; color: var(--white); font-size: 40px; }
  .brand-back .brand-mark { width: 46px; height: 46px; border-width: 5px; }
  .website-back {
    display: flex; align-items: center; gap: 14px;
    color: var(--white); font-size: 14px; letter-spacing: 0.12em;
  }
  .website-back .rule { width: 52px; height: 1px; background: var(--white); opacity: 0.8; }
</style>
</head>
<body>

<section class="card card-front">
  <svg class="front-bands" viewBox="0 0 560 320" preserveAspectRatio="none" aria-hidden="true">
    <path d="M0 268 H300 C330 268 338 248 362 248 H560 V320 H0 Z" fill="var(--navy)"/>
    <path d="M330 262 C340 238 350 222 378 222 H560 V262 Z" fill="var(--sky)"/>
    <path d="M318 226 C332 212 345 206 372 206 H560 V214 H374 C352 214 340 220 328 232 Z" fill="var(--navy)"/>
  </svg>

  <div class="brand brand-front"><span class="brand-mark"></span>SkyvornQ</div>

  <address class="contact-address">
    4827 Trellis Hollow Road,<br>
    Calderwick Bay, Westmarch, 70412
  </address>

  <div class="website-front">www.skyvornq.com</div>

  <div class="person">
    <div class="person-name">Daniel Reyes</div>
    <div class="person-title">President</div>
    <div class="contact-row">
      <svg viewBox="0 0 12 12" aria-hidden="true"><path d="M2 1 L4.5 1 L5.5 3.5 L4 4.6 C4.8 6.3 5.7 7.2 7.4 8 L8.5 6.5 L11 7.5 L11 10 C6 10.5 1.5 6 2 1 Z" fill="var(--navy)"/></svg>
      001 555 0148
    </div>
    <div class="contact-row">
      <svg viewBox="0 0 12 12" aria-hidden="true"><rect x="3" y="0.8" width="6.4" height="10.4" rx="1.2" fill="none" stroke="var(--navy)" stroke-width="1.3"/></svg>
      001 555 0148
    </div>
  </div>

  <div class="email">
    <svg viewBox="0 0 13 10" aria-hidden="true"><rect x="0.5" y="0.5" width="12" height="9" fill="var(--white)"/><path d="M0.5 0.5 L6.5 5.5 L12.5 0.5" fill="none" stroke="var(--navy)" stroke-width="1"/></svg>
    info@skyvornq.com
  </div>
</section>

<section class="card card-back">
  <div class="back-content">
    <div class="brand brand-back"><span class="brand-mark"></span>SkyvornQ</div>
    <div class="website-back"><span class="rule"></span>www.skyvornq.com<span class="rule"></span></div>
  </div>
</section>

</body>
</html>
```